Harrow Hide Revival Product Label

We need a design for a label to be used on bottles of leather cleaner and conditioner products that will be used in curated kits. We would like it to incorporate our business logo as well as have an area that we can fill in later with the appropriate product name as needed. We would like to see designs that use shades of brown, but we are open to other colors often seen in leather. I am including the Harrow Hide business Logo below, however again we would prefer to have the label in various shades of browns, rather than the red and grey, more like the mock-up that I am also attaching.

*** I am attaching examples of the types of bottles that will be used. They vary in size from 8 oz to 16 oz. if you are designing a label for a spray bottle they are from 16-32 oz. ***

```html
<!DOCTYPE html>
<html lang="en">
<head>
<meta charset="utf-8">
<title>Harrow Hide Revival – Product Labels</title>
<link rel="stylesheet" href="https://fonts.googleapis.com/css2?family=Oswald:wght@400;600;700&display=swap">
<style>
  :root{
    --backdrop:#d8d8d8;
    --leather-dark:#3a2412;
    --leather-mid:#5a3a20;
    --leather-light:#7d5a3c;
    --gold:#d9b44a;
    --gold-deep:#9a7420;
    --cap-black:#0c0c0c;
    --ink-white:#f4f1ec;
    --stitch:#e8dccb;
  }
  *{box-sizing:border-box;margin:0;padding:0}
  html,body{width:1200px;height:1129px;overflow:hidden}
  body{
    background:var(--backdrop);
    font-family:"Oswald",sans-serif;
    position:relative;
  }
  .label{
    position:absolute;
    top:150px;
    width:440px;
    height:830px;
    background:var(--cap-black);
    box-shadow:0 18px 40px rgba(0,0,0,.25);
    overflow:hidden;
  }
  .label--conditioner{left:110px}
  .label--cleaner{left:650px}
  .label__field{
    position:absolute;
    inset:40px 0;
    background:
      radial-gradient(ellipse at 60% 30%, var(--leather-light) 0%, rgba(125,90,60,0) 55%),
      radial-gradient(ellipse at 30% 75%, rgba(125,90,60,.6) 0%, rgba(125,90,60,0) 50%),
      linear-gradient(180deg, var(--leather-mid), var(--leather-dark) 60%, var(--leather-mid));
  }
  .gold-band{
    position:absolute;left:0;right:0;height:7px;
    background:linear-gradient(90deg,var(--gold-deep),var(--gold),#f3dc8a,var(--gold),var(--gold-deep));
  }
  .gold-band--top{top:40px}
  .gold-band--bottom{bottom:40px}
  .brand{
    position:absolute;top:110px;left:0;right:0;
    display:flex;align-items:center;justify-content:center;gap:14px;
  }
  .brand__mark{
    width:34px;height:34px;border-radius:50%;
    background:var(--ink-white);
  }
  .brand__name{
    color:var(--ink-white);
    font-weight:400;
    font-size:24px;
    letter-spacing:3px;
    text-transform:uppercase;
  }
  .badge{
    position:absolute;top:215px;left:50%;
    width:330px;height:250px;
    transform:translateX(-50%);
  }
  .badge svg{position:absolute;inset:0}
  .badge__text{
    position:absolute;inset:0;
    display:flex;flex-direction:column;align-items:center;justify-content:center;
    color:var(--ink-white);text-transform:uppercase;line-height:.95;
  }
  .badge__word{font-weight:700;font-size:74px;letter-spacing:1px}
  .badge__product{font-weight:600;font-size:40px;letter-spacing:1px}
  .tagline{
    position:absolute;top:520px;left:0;right:0;
    text-align:center;color:var(--ink-white);
    font-weight:600;font-size:38px;line-height:1.05;
  }
  .volume{
    position:absolute;bottom:90px;left:0;right:0;
    text-align:center;color:var(--ink-white);
    font-weight:400;font-size:24px;letter-spacing:1px;
  }
</style>
</head>
<body>

  <section class="label label--conditioner">
    <div class="label__field" role="img" aria-label="Brown leather-toned background with faint flourish pattern"></div>
    <div class="gold-band gold-band--top"></div>
    <div class="gold-band gold-band--bottom"></div>
    <div class="brand"><span class="brand__mark"></span><span class="brand__name">Harrow Hide Revival, Inc</span></div>
    <div class="badge">
      <svg viewBox="0 0 330 250" aria-hidden="true">
        <path d="M40 20 H290 Q290 45 315 45 V205 Q290 205 290 230 H40 Q40 205 15 205 V45 Q40 45 40 20 Z"
              fill="none" stroke="var(--stitch)" stroke-width="2" stroke-dasharray="7 5"/>
      </svg>
      <div class="badge__text">
        <span class="badge__word">Leather</span>
        <span class="badge__product">Conditioner</span>
      </div>
    </div>
    <p class="tagline">Makes Leather<br>Last Longer</p>
    <p class="volume">16 US FL. OZ 473 ML</p>
  </section>

  <section class="label label--cleaner">
    <div class="label__field" role="img" aria-label="Brown leather-toned background with faint flourish pattern"></div>
    <div class="gold-band gold-band--top"></div>
    <div class="gold-band gold-band--bottom"></div>
    <div class="brand"><span class="brand__mark"></span><span class="brand__name">Harrow Hide Revival, Inc</span></div>
    <div class="badge">
      <svg viewBox="0 0 330 250" aria-hidden="true">
        <path d="M40 20 H290 Q290 45 315 45 V205 Q290 205 290 230 H40 Q40 205 15 205 V45 Q40 45 40 20 Z"
              fill="none" stroke="var(--stitch)" stroke-width="2" stroke-dasharray="7 5"/>
      </svg>
      <div class="badge__text">
        <span class="badge__word">Leather</span>
        <span class="badge__product">Cleaner</span>
      </div>
    </div>
    <p class="tagline">Makes Leather<br>Last Longer</p>
    <p class="volume">16 US FL. OZ 473 ML</p>
  </section>

</body>
</html>
```